ULMIRA card Technical Architecture

Hello everyone ULMIRA: It is a consulting firm in Architecture and Construction. I require a card duplexing, sober, elegant, classic but not boring. Update 1: Use the following data for the card. Name: Gonzalo Pereda Mauricio Villalta Position: COO Twitter: @ulmiraAT Homepage: ulmira-example.com home address not include the participation of all thank you.

Target Market(s)

Construction companies, Architects and Consulting Engineers

Industry/Entity Type

Consulting

Contact Information for Business Card

Los campos que debe tener:
Nombre, Cargo, email, homepage y twitter

Font styles to use
Serif
Sans Serif
Other font styles liked:
• Me gustan playfair display, open sans y roboto, pero estoy sujeto a sus propuestas

Requirements
Must have
• Colors: Present combined proposals in white, red, gray and black Update 1: The two names must be clearly differentiated from the two surnames
Nice to have
• They are free to present their best proposals. I will bring them immediate feedback to the extent you can go see their designs. Complete data for card and logo files will give the winner the

```html
<!DOCTYPE html>
<html lang="es">
<head>
<meta charset="utf-8">
<title>ULMIRA – Arquitectura Técnica business card</title>
<link rel="stylesheet" href="https://fonts.googleapis.com/css2?family=Open+Sans:wght@300;400;600&display=swap">
<style>
  :root {
    --bg: #ece9e7;
    --white: #ffffff;
    --red-light: #e8647c;
    --red: #b0182c;
    --red-dark: #5c0008;
    --ink: #111111;
    --tag-red: #9c1a26;
  }
  * { margin: 0; padding: 0; box-sizing: border-box; }
  html, body { width: 1200px; height: 900px; overflow: hidden; }
  body {
    position: relative;
    background: var(--bg);
    font-family: "Open Sans", Arial, sans-serif;
  }
  .card {
    position: absolute;
    overflow: hidden;
    box-shadow: 0 6px 18px rgba(0,0,0,.18);
  }
  /* Front side */
  .card-front {
    left: 237px; top: 60px; width: 556px; height: 345px;
    background: linear-gradient(180deg, var(--red-light) 0%, var(--red) 35%, var(--red-dark) 75%, #4a0006 100%);
    color: var(--white);
  }
  .front-decor { position: absolute; left: 0; top: 0; width: 320px; height: 345px; }
  .front-brand {
    position: absolute; right: 30px; top: 52px; text-align: right;
  }
  .brand-name {
    font-weight: 300; font-size: 31px; letter-spacing: 9px; line-height: 1;
    margin-right: -9px;
  }
  .brand-tagline {
    font-weight: 400; font-size: 12.5px; letter-spacing: 2.6px; margin-top: 10px;
    text-transform: uppercase;
  }
  .person { position: absolute; right: 28px; top: 154px; text-align: right; }
  .person-name { font-weight: 600; font-size: 19px; line-height: 26px; }
  .person-role { font-weight: 400; font-size: 15px; line-height: 20px; }
  .contact-list { position: absolute; right: 28px; top: 222px; list-style: none; }
  .contact-list li {
    display: flex; justify-content: flex-end; align-items: center;
    font-size: 15px; line-height: 20px; gap: 10px;
  }
  .contact-icon { width: 11px; height: 11px; flex: none; }
  /* Back side */
  .card-back {
    left: 457px; top: 518px; width: 560px; height: 344px;
    background: var(--white);
    text-align: center;
  }
  .back-mark {
    width: 54px; height: 54px; border-radius: 50%;
    background: linear-gradient(160deg, var(--red-light), var(--red-dark));
    margin: 94px auto 0;
  }
  .back-name {
    font-weight: 300; font-size: 44px; letter-spacing: 12px; color: var(--ink);
    margin-top: 18px; line-height: 1; margin-right: -12px;
  }
  .back-tagline {
    font-size: 15px; letter-spacing: 3px; color: var(--tag-red);
    margin-top: 14px; text-transform: uppercase;
  }
</style>
</head>
<body>
  <section class="card card-front">
    <svg class="front-decor" role="img" aria-label="Brand decoration area in white and red tones" viewBox="0 0 320 345">
      <defs>
        <linearGradient id="decorFill" x1="0" y1="0" x2="1" y2="1">
          <stop offset="0" stop-color="#ffffff"/>
          <stop offset="1" stop-color="#f4dde1"/>
        </linearGradient>
      </defs>
      <polygon points="0,0 120,0 320,345 0,345" fill="url(#decorFill)"/>
    </svg>
    <div class="front-brand">
      <div class="brand-name">ULMIRA</div>
      <div class="brand-tagline">Arquitectura Técnica</div>
    </div>
    <div class="person">
      <div class="person-name">Lucas Moreno</div>
      <div class="person-role">Managing Director</div>
    </div>
    <ul class="contact-list">
      <li>555 010 234
        <svg class="contact-icon" viewBox="0 0 11 11" aria-hidden="true"><rect x="3" y="0.5" width="5" height="10" rx="1" fill="none" stroke="#fff" stroke-width="1.2"/><rect x="4.7" y="8.3" width="1.6" height="1" fill="#fff"/></svg>
      </li>
      <li>info@ulmira-example.com
        <svg class="contact-icon" viewBox="0 0 11 11" aria-hidden="true"><rect x="0.5" y="2" width="10" height="7" fill="#fff"/><path d="M0.5 2 L5.5 6 L10.5 2" fill="none" stroke="#5c0008" stroke-width="1"/></svg>
      </li>
      <li>www.ulmira-example.com
        <svg class="contact-icon" viewBox="0 0 11 11" aria-hidden="true"><circle cx="5.5" cy="5.5" r="5" fill="#fff"/><path d="M0.5 5.5 H10.5 M5.5 0.5 C3 3 3 8 5.5 10.5 C8 8 8 3 5.5 0.5" fill="none" stroke="#5c0008" stroke-width="0.8"/></svg>
      </li>
      <li>@ulmiraAT
        <svg class="contact-icon" viewBox="0 0 11 11" aria-hidden="true"><rect x="0.5" y="0.5" width="10" height="10" rx="1.5" fill="#fff"/></svg>
      </li>
    </ul>
  </section>

  <section class="card card-back">
    <div class="back-mark"></div>
    <div class="back-name">ULMIRA</div>
    <div class="back-tagline">Arquitectura Técnica</div>
  </section>
</body>
</html>
```